Local fast-growing company in the service sector

We are looking for a modern business card design, which should also appear on our letterheads

Target Market(s)

Private and industrial sectors

Contact Information for Business Card

Vorname Name
Kellberger Str. 18
73614 Lindenfeld
Tel.: 07146-839214-0
Name@agentur-kvtl.de

Colors
9d9d9d
919191
aaaaaa

Requirements
Must have
• The logo (file) in silver

```html
<!DOCTYPE html>
<html lang="de">
<head>
<meta charset="utf-8">
<title>KVTL Visitenkarte</title>
<link rel="stylesheet" href="https://fonts.googleapis.com/css2?family=Open+Sans:wght@400;600;700&display=swap">
<style>
  :root {
    --stage: #ececec;
    --card-dark: #58595b;
    --frost-light: #eeeeee;
    --frost-mid: #dcdcdc;
    --silver: #9d9d9d;
    --silver-deep: #919191;
    --silver-soft: #aaaaaa;
    --text-light: #f2f2f2;
  }
  * { box-sizing: border-box; margin: 0; padding: 0; }
  html, body { width: 1200px; height: 900px; overflow: hidden; }
  body {
    background: var(--stage);
    font-family: "Open Sans", Arial, sans-serif;
    position: relative;
  }
  .card {
    position: absolute;
    border-radius: 30px;
    overflow: hidden;
    background: linear-gradient(135deg, var(--frost-light), var(--frost-mid));
  }
  .card--front { left: 200px; top: 35px; width: 585px; height: 363px; }
  .card--back  { left: 388px; top: 505px; width: 567px; height: 352px; }

  .card__panel { position: absolute; background: var(--card-dark); }
  .card--front .panel-side   { left: 0; top: 0; width: 262px; height: 100%; }
  .card--front .panel-base   { left: 0; bottom: 0; width: 490px; height: 36px; }
  .card--back  .panel-side   { right: 0; top: 0; width: 255px; height: 100%; }
  .card--back  .panel-top    { right: 0; top: 0; width: 410px; height: 36px; }

  .holder-name {
    position: absolute; left: 28px; top: 50px;
    color: var(--text-light); font-size: 18px; font-weight: 600; letter-spacing: 0.2px;
  }
  .address {
    position: absolute; left: 26px; top: 198px;
    color: var(--text-light); font-size: 15px; line-height: 22px;
  }
  .contact-list {
    position: absolute; left: 26px; top: 252px; list-style: none;
    color: var(--text-light); font-size: 15px; line-height: 22px;
  }
  .contact-list li { display: flex; align-items: center; gap: 6px; }
  .contact-list svg { width: 15px; height: 15px; flex: none; }

  .wordmark {
    position: absolute; color: var(--silver); font-weight: 700; line-height: 1;
  }
  .card--front .wordmark { left: 345px; top: 150px; }
  .wordmark__name { display: block; font-size: 44px; letter-spacing: 1px; }
  .wordmark__web  { display: block; font-size: 14px; font-weight: 700; margin-top: 2px; }
  .card--back .wordmark {
    left: 50px; top: 140px; transform: scaleX(-1); color: var(--silver-soft); opacity: 0.45;
  }
  .card--back .wordmark__name { font-size: 36px; }
  .card--back .wordmark__web  { font-size: 12px; }

  .back-web {
    position: absolute; right: 38px; bottom: 48px;
    color: var(--text-light); font-size: 17px;
  }
</style>
</head>
<body>
  <section class="card card--front" aria-label="Visitenkarte Vorderseite">
    <div class="card__panel panel-side"></div>
    <div class="card__panel panel-base"></div>
    <h1 class="holder-name">VORNAME NAME</h1>
    <p class="address">Kellberger Str. 18<br>73614 Lindenfeld</p>
    <ul class="contact-list">
      <li>
        <svg viewBox="0 0 16 16" aria-hidden="true"><path fill="#f2f2f2" d="M3.5 1.5l2.3 2.6-1.3 1.6c.9 1.9 2.3 3.3 4.2 4.2l1.6-1.3 2.6 2.3-1.2 2c-5.6-.4-9.8-4.6-10.2-10.2z"/></svg>
        07146-839214-0
      </li>
      <li>
        <svg viewBox="0 0 16 16" aria-hidden="true"><rect x="1.5" y="3.5" width="13" height="9" fill="#f2f2f2"/><path d="M1.5 3.5l6.5 5 6.5-5" fill="none" stroke="#58595b" stroke-width="1.2"/></svg>
        Name@agentur-kvtl.de
      </li>
      <li>
        <svg viewBox="0 0 16 16" aria-hidden="true"><circle cx="8" cy="8" r="6.5" fill="#f2f2f2"/><path d="M1.5 8h13M8 1.5c-2.5 3-2.5 10 0 13M8 1.5c2.5 3 2.5 10 0 13" fill="none" stroke="#58595b" stroke-width="1"/></svg>
        www.agentur-kvtl.de
      </li>
    </ul>
    <div class="wordmark">
      <span class="wordmark__name">KVTL</span>
      <span class="wordmark__web">agentur-kvtl.de</span>
    </div>
  </section>

  <section class="card card--back" aria-label="Visitenkarte Rückseite">
    <div class="card__panel panel-side"></div>
    <div class="card__panel panel-top"></div>
    <div class="wordmark" aria-hidden="true">
      <span class="wordmark__name">KVTL</span>
      <span class="wordmark__web">agentur-kvtl.de</span>
    </div>
    <p class="back-web">www.agentur-kvtl.de</p>
  </section>
</body>
</html>
```